Investment firm needs refreshed corporate powerpoint slides design

We need a new and refreshed powerpoint template for our corporate investment deck. We are a technology private equity group that primarily invests in fast growing software companies and we would like to reflect that in a modern and light blue / transparant / white powerpoint and fonts template. I have also attached our old investor deck as a guideline and also check out our website to get an idea of what we do and what type of companies we invested in. Please note that our website is old and so our presentation should be a refreshed "2017" modern design, not a copy / paste of our website design and graphics.
Updates

Project Deadline Extended Reason: I'm extending the deadline to February 27, but we would ideally receive something by the end of this week.Please submit updates. Thanks Added Tuesday, February 21, 2017

Target Market(s)

Investors such as high net worth individuals, pension funds, banks, financial advisors

Industry/Entity Type

Investment

Colors
33a6d7
85cae6
cfeae6
edf8f6
ffffff
fff3d1
86cfc6

Requirements
Must have
• We let you be creative, we trust you have seen more investment presentations before.
Nice to have
• Pre-built models, flow charts, graphs, charts, etc.
Should not have
• Fancy or edgy images, this has to be a modern, fresh and trustworthy looking powerpoint template. No stock images, if you do use stock images for background purposes please be creative! :-)

```html
<!DOCTYPE html>
<html lang="en">
<head>
<meta charset="utf-8">
<title>Northvale Growth – Investor Deck Template</title>
<link href="https://fonts.googleapis.com/css2?family=Open+Sans:ital,wght@0,400;0,600;0,700;1,400&display=swap" rel="stylesheet">
<style>
:root{
  --blue:#33a6d7;--sky:#85cae6;--mint:#cfeae6;--ice:#edf8f6;--white:#fff;
  --cream:#fff3d1;--teal:#86cfc6;--navy:#1d5e99;--ink:#222;--grey:#6d6d6d;--line:#d9dfe3;
}
*{box-sizing:border-box}
html,body{margin:0;width:1200px;height:1104px;overflow:hidden;background:#fff;font-family:'Open Sans',sans-serif}
.board{position:relative;width:1200px;height:1104px}
.slide{position:absolute;width:226px;height:170px;background:var(--white);overflow:hidden;box-shadow:0 0 2px rgba(0,0,0,.28)}
.abs{position:absolute;margin:0}
.kicker{position:absolute;left:8px;top:5px;margin:0;font-size:3.6px;font-style:italic;color:#888}
.title{position:absolute;left:8px;top:10px;margin:0;font-size:5px;font-weight:700;color:var(--ink);text-transform:uppercase;white-space:nowrap}
.num{position:absolute;right:6px;top:4px;width:7px;height:8px;background:var(--sky);color:#fff;font-size:4px;line-height:8px;text-align:center}
.foot{position:absolute;left:0;bottom:0;width:100%;height:14px}
.brand{position:absolute;left:7px;bottom:2px;font-size:9.5px;color:var(--navy);font-weight:400;line-height:1}
.foot-bar{position:absolute;left:50px;right:0;bottom:3px;height:5px;background:var(--navy)}
.tx{font-size:3.5px;line-height:1.4;color:var(--grey);margin:0}
.hd{font-size:3.8px;font-weight:700;color:var(--blue);margin:0;text-transform:uppercase}
.big-num{font-size:10px;color:var(--blue);margin:0;line-height:1}
.band{position:absolute;background:var(--blue)}
.cell-head{background:var(--sky);color:#fff;font-size:3.6px;font-weight:700;padding:2px 3px}
table.data{position:absolute;border-collapse:collapse;font-size:3.6px;color:#555}
table.data th{background:var(--sky);color:#fff;font-weight:700;padding:2px 3px;text-align:left}
table.data td{padding:1.6px 3px;border-bottom:.5px solid var(--line)}
table.data tr.total td{font-weight:700;color:var(--ink)}
table.data td.hl{color:var(--blue);font-weight:700}
.img-fill{position:absolute}
ul.tx{padding-left:6px}
.box{position:absolute;border:.6px solid var(--sky);font-size:3.2px;color:#444;text-align:center;line-height:1.3;padding:1px}
.box.fill{background:var(--blue);color:#fff;border-color:var(--blue)}
</style>
</head>
<body>
<main class="board">

<!-- Row 1 -->
<section class="slide cover" style="left:11px;top:8px">
  <svg class="abs" style="left:0;top:0" width="226" height="170" aria-hidden="true">
    <polygon points="226,0 226,130 140,170 226,170" fill="#e7f4fa"/>
    <polygon points="226,30 150,110 226,165" fill="var(--sky)" opacity=".5"/>
    <polygon points="226,60 175,110 226,150" fill="var(--blue)"/>
  </svg>
  <h1 class="abs" style="left:16px;top:30px;font-size:11px;color:var(--navy);font-weight:700">Northvale Growth</h1>
  <p class="abs tx" style="left:16px;top:47px;font-style:italic;font-size:4.5px">Introduction to Team and Track Record</p>
  <p class="abs tx" style="left:16px;top:56px;font-size:4.5px">For US Investor</p>
  <p class="abs" style="left:16px;top:64px;font-size:4.5px;font-weight:700;color:#333">Presented by: John Doe</p>
  <div class="band" style="left:16px;top:84px;width:106px;height:8px;background:var(--navy);color:#fff;font-size:4px;font-weight:700;text-align:center;line-height:8px">Feb 2017</div>
  <p class="abs" style="left:146px;top:94px;font-size:22px;color:var(--navy);line-height:1">Harlow</p>
  <svg class="abs" style="left:40px;top:148px" width="8" height="8" aria-hidden="true"><circle cx="4" cy="4" r="3.4" fill="none" stroke="var(--blue)" stroke-width=".7"/></svg>
  <p class="abs tx" style="left:28px;top:158px;font-size:3.5px">info@harlowcap.com</p>
  <svg class="abs" style="left:96px;top:148px" width="8" height="8" aria-hidden="true"><circle cx="4" cy="4" r="3.4" fill="none" stroke="var(--blue)" stroke-width=".7"/></svg>
  <p class="abs tx" style="left:88px;top:158px;font-size:3.5px">1-555-0182</p>
</section>

<section class="slide cover-alt" style="left:249px;top:8px">
  <div class="img-fill" role="img" aria-label="City skyline with a rocket launching into clouds" style="left:0;top:0;width:226px;height:88px;background:linear-gradient(180deg,#2f7fc1,#85cae6 70%,#edf8f6)"></div>
  <h1 class="abs" style="left:12px;top:20px;font-size:11px;color:#fff;font-weight:700">Northvale Growth</h1>
  <p class="abs" style="left:12px;top:36px;font-size:4.5px;color:#fff;font-style:italic">Introduction to Team and Track Record</p>
  <p class="abs tx" style="left:96px;top:108px;font-size:4.5px">For US Investor</p>
  <p class="abs" style="left:96px;top:116px;font-size:4.5px;font-weight:700;color:#333">Presented by: John Doe</p>
  <div class="band" style="left:96px;top:133px;width:84px;height:8px;background:var(--navy);color:#fff;font-size:4px;font-weight:700;text-align:center;line-height:8px">Feb 2017</div>
  <footer class="foot"><span class="brand">Harlow</span></footer>
</section>

<section class="slide agenda" style="left:487px;top:8px">
  <span class="num">4</span>
  <div class="band" style="left:0;top:56px;width:80px;height:7px;background:var(--sky)"></div>
  <p class="kicker" style="left:80px;top:47px">Place the sub header here</p>
  <h2 class="title" style="left:80px;top:54px">Presentation Agenda</h2>
  <ul class="abs tx" style="left:104px;top:72px">
    <li>Executive Summary</li><li>Differentiated Model</li><li>Track Record</li><li>Summary of Terms</li><li>Appendix</li>
  </ul>
  <ul class="abs tx" style="left:160px;top:80px">
    <li>Team and Advisory Board</li><li>Target Profile</li><li>Proprietary Company and</li><li>Executive Sourcing</li><li>Operational Focus</li>
  </ul>
  <footer class="foot"><span class="brand">Harlow</span><i class="foot-bar"></i></footer>
</section>

<section class="slide overview" style="left:725px;top:8px">
  <p class="kicker">Place the sub header here</p><h2 class="title">Northvale Growth Overview</h2><span class="num">5</span>
  <div class="abs" style="left:10px;top:32px;width:210px;display:grid;grid-template-columns:repeat(3,1fr);gap:10px 8px">
    <div><p class="big-num">01</p><p class="hd" style="font-weight:400">Some title here</p><p class="tx">New management company and carry ownership held by the US team.</p></div>
    <div><p class="big-num">02</p><p class="hd" style="font-weight:400">Some title here</p><p class="tx">New management company and carry ownership held by the US team.</p></div>
    <div><p class="big-num">03</p><p class="hd" style="font-weight:400">Some title here</p><p class="tx">New management company and carry ownership held by the US team.</p></div>
    <div><p class="big-num">04</p><p class="hd" style="font-weight:400">Some title here</p><p class="tx">New management company and carry ownership held by the US team.</p></div>
    <div><p class="big-num">05</p><p class="hd" style="font-weight:400">Some title here</p><p class="tx">New management company and carry ownership held by the US team.</p></div>
    <div><p class="big-num">06</p><p class="hd" style="font-weight:400">Some title here</p><p class="tx">New management company and carry ownership held by the US team.</p></div>
  </div>
  <footer class="foot"><span class="brand">Harlow</span><i class="foot-bar"></i></footer>
</section>

<section class="slide exec-summary" style="left:963px;top:8px">
  <p class="kicker">Place the sub header here</p><h2 class="title">Executive Summary</h2><span class="num">5</span>
  <div class="img-fill" role="img" aria-label="Soft blue city background band" style="left:0;top:50px;width:226px;height:42px;background:linear-gradient(90deg,#2a88c4,#5cb5de)"></div>
  <div class="abs" style="left:6px;top:56px;width:214px;display:grid;grid-template-columns:repeat(4,1fr);text-align:center;color:#fff;font-size:3.2px;font-weight:700">
    <div><svg width="12" height="12" aria-hidden="true"><rect x="2" y="2" width="8" height="6" fill="none" stroke="#fff" stroke-width=".7"/></svg><br>OVER A DECADE OF SUPERIOR VALUE CREATION</div>
    <div><svg width="12" height="12" aria-hidden="true"><circle cx="6" cy="6" r="4" fill="none" stroke="#fff" stroke-width=".7"/></svg><br>ACHIEVING SUPERIOR RETURNS</div>
    <div><svg width="12" height="12" aria-hidden="true"><path d="M2 4h8M2 8h8" stroke="#fff" stroke-width=".8"/></svg><br>REPEATABLE SOURCING MODEL</div>
    <div><svg width="12" height="12" aria-hidden="true"><rect x="3" y="3" width="6" height="6" fill="none" stroke="#fff" stroke-width=".7"/></svg><br>BUILDING SUCCESSFUL BUSINESSES</div>
  </div>
  <div class="abs" style="left:8px;top:98px;width:212px;display:grid;grid-template-columns:repeat(4,1fr);gap:4px">
    <ul class="tx"><li>Proven, capital efficient executive CEO</li><li>Founders help source</li><li>Work closely with teams</li></ul>
    <ul class="tx"><li>Proven, capital efficient executive CEO</li><li>Founders help source</li><li>Work closely with teams</li></ul>
    <ul class="tx"><li>Proven, capital efficient executive CEO</li><li>Founders help source</li><li>Work closely with teams</li></ul>
    <ul class="tx"><li>Proven, capital efficient executive CEO</li><li>Founders help source</li><li>Work closely with teams</li></ul>
  </div>
  <footer class="foot"><span class="brand">Harlow</span><i class="foot-bar"></i></footer>
</section>

<!-- Row 2 -->
<section class="slide returns" style="left:11px;top:190px">
  <p class="kicker">Place the sub header here</p><h2 class="title">Achieving Superior Returns</h2><span class="num">6</span>
  <p class="abs" style="left:12px;top:21px;font-size:4.5px;font-weight:600;color:#333">US High Growth Buyout/Equity Portfolio 2004 through June 2016</p>
  <p class="abs" style="left:36px;top:48px;font-size:4.5px;font-weight:700;color:#333">Harlow US Growth Returns</p>
  <p class="abs tx" style="left:40px;top:56px">■ Invested &nbsp; ■ Total Value</p>
  <svg class="abs" style="left:18px;top:64px" width="100" height="62" aria-hidden="true">
    <line x1="0" y1="60" x2="100" y2="60" stroke="#999" stroke-width=".5"/>
    <rect x="18" y="22" width="24" height="38" fill="var(--sky)"/>
    <rect x="60" y="10" width="24" height="50" fill="var(--sky)"/>
    <polyline points="4,36 30,36 72,8 96,8" fill="none" stroke="#333" stroke-width=".5"/>
  </svg>
  <p class="abs tx" style="left:34px;top:127px">Invested</p><p class="abs tx" style="left:76px;top:127px">Total Value</p>
  <div class="abs" style="left:134px;top:44px"><p class="big-num">01</p><p class="hd" style="font-weight:400">Some title here</p><ol class="tx" style="padding-left:6px"><li>Lorem ipsum dolor sit</li><li>diam donec neque</li><li>ante rutrum proin</li><li>amet nunc dolor</li></ol></div>
  <div class="abs" style="left:134px;top:88px"><p class="big-num">02</p><p class="hd" style="font-weight:400">Some title here</p><ol class="tx" style="padding-left:6px"><li>Lorem ipsum dolor sit</li><li>diam donec neque</li><li>ante rutrum proin</li><li>amet nunc dolor</li></ol></div>
  <p class="abs tx" style="left:12px;top:138px;width:200px;font-size:2.6px">Gross returns shown for illustration; past performance is not indicative of future results. Returns reflect realized and unrealized value as of period end.</p>
  <footer class="foot"><span class="brand">Harlow</span><i class="foot-bar"></i></footer>
</section>

<section class="slide exits" style="left:249px;top:190px">
  <p class="kicker">Place the sub header here</p><h2 class="title">Lower middle market provides the majority of tech exits...</h2><span class="num">7</span>
  <table class="data" style="left:0;top:42px;width:226px">
    <tr><th style="padding-left:20px">Exit Range</th><th>Total Deals</th><th>%</th></tr>
    <tr><td style="padding-left:20px">$500M+</td><td>150</td><td>8%</td></tr>
    <tr><td style="padding-left:20px">$300-500M</td><td>141</td><td>8%</td></tr>
    <tr><td style="padding-left:20px">$150-300M</td><td>272</td><td class="hl">15%</td></tr>
    <tr><td style="padding-left:20px">$50-150M</td><td>568</td><td class="hl">32%</td></tr>
    <tr><td style="padding-left:20px">$20-50M</td><td>661</td><td class="hl">37%</td></tr>
    <tr class="total"><td style="padding-left:20px">TOTALS</td><td>1792</td><td>100%</td></tr>
  </table>
  <div class="abs" style="left:14px;top:118px;width:200px;display:grid;grid-template-columns:repeat(3,1fr);gap:6px;text-align:center">
    <div><p class="hd" style="font-weight:400">Some title here</p><p class="tx">Lorem ipsum dolor sit amet, diam donec neque nisl nibh.</p></div>
    <div><p class="hd" style="font-weight:400">Some title here</p><p class="tx">Lorem ipsum dolor sit amet, diam donec neque nisl nibh.</p></div>
    <div><p class="hd" style="font-weight:400">Some title here</p><p class="tx">Lorem ipsum dolor sit amet, diam donec neque nisl nibh.</p></div>
  </div>
  <footer class="foot"><span class="brand">Harlow</span><i class="foot-bar"></i></footer>
</section>

<section class="slide pyramid" style="left:487px;top:190px">
  <p class="kicker">Place the sub header here</p><h2 class="title">With strong upside for higher value outcomes</h2><span class="num">8</span>
  <p class="abs tx" style="left:150px;top:28px">M&amp;A Private Tech Companies 2006-2015</p>
  <svg class="abs" style="left:4px;top:36px" width="124" height="120" aria-hidden="true">
    <polygon points="62,4 80,28 44,28" fill="#1d6fa8"/>
    <polygon points="44,30 80,30 95,50 29,50" fill="#2a88c4"/>
    <polygon points="29,52 95,52 110,72 14,72" fill="var(--blue)"/>
    <polygon points="14,74 110,74 122,94 2,94" fill="var(--sky)"/>
    <polygon points="2,96 122,96 122,118 2,118" fill="var(--mint)"/>
  </svg>
  <p class="abs" style="left:34px;top:75px;width:70px;text-align:center;font-size:3.4px;color:#fff">Crestline, Tidewater, Arbor</p>
  <p class="abs" style="left:22px;top:97px;width:94px;text-align:center;font-size:3.4px;color:#fff">Summit Ridge, Larkspur, Fenwick</p>
  <p class="abs" style="left:10px;top:119px;width:118px;text-align:center;font-size:3.4px;color:#fff"><b>Northvale</b> Bellmont, Greyfield</p>
  <p class="abs" style="left:6px;top:141px;width:124px;text-align:center;font-size:3.4px;color:#446">Venture, Angel, Seed Funds</p>
  <table class="data" style="left:130px;top:46px;width:94px">
    <tr><th>Exit Range</th><th>Total Deals</th><th>%</th></tr>
    <tr><td>$500M+</td><td>150</td><td>8%</td></tr>
    <tr><td>$300-500M</td><td>141</td><td>8%</td></tr>
    <tr><td>$150-300M</td><td>272</td><td>15%</td></tr>
    <tr><td>$50-150M</td><td>568</td><td>32%</td></tr>
    <tr><td>$20-50M</td><td>661</td><td>37%</td></tr>
  </table>
  <footer class="foot"><span class="brand">Harlow</span><i class="foot-bar"></i></footer>
</section>

<section class="slide bubbles" style="left:725px;top:190px">
  <p class="kicker">Place the sub header here</p><h2 class="title">Lower middle market offers high value creation for growth</h2><span class="num">9</span>
  <svg class="abs" style="left:8px;top:26px" width="212" height="84" aria-hidden="true">
    <g stroke="#e3e6e8" stroke-width=".5">
      <line x1="14" y1="6" x2="210" y2="6"/><line x1="14" y1="20" x2="210" y2="20"/><line x1="14" y1="34" x2="210" y2="34"/><line x1="14" y1="48" x2="210" y2="48"/><line x1="14" y1="62" x2="210" y2="62"/>
      <line x1="60" y1="4" x2="60" y2="72"/><line x1="110" y1="4" x2="110" y2="72"/><line x1="160" y1="4" x2="160" y2="72"/>
    </g>
    <line x1="14" y1="72" x2="210" y2="72" stroke="#999" stroke-width=".5"/>
    <circle cx="30" cy="54" r="8" fill="var(--blue)"/>
    <circle cx="80" cy="28" r="8" fill="var(--cream)" stroke="#e8d79a" stroke-width=".5"/>
    <circle cx="136" cy="22" r="8" fill="var(--mint)"/>
    <circle cx="186" cy="14" r="8" fill="var(--blue)"/>
    <rect x="14" y="64" width="26" height="4" fill="var(--sky)"/>
    <rect x="92" y="36" width="28" height="4" fill="#cfd4d8"/>
    <rect x="146" y="32" width="28" height="4" fill="#cfd4d8"/>
    <g fill="#555" font-size="3.2"><text x="0" y="8">$80</text><text x="0" y="22">$60</text><text x="0" y="36">$40</text><text x="0" y="50">$20</text><text x="0" y="64">$10</text></g>
    <g fill="#555" font-size="4"><text x="22" y="80">2014</text><text x="74" y="80">2015</text><text x="130" y="80">2016</text><text x="180" y="80">2017</text></g>
  </svg>
  <p class="abs" style="left:0;top:111px;width:226px;text-align:center;font-size:4.5px;color:var(--blue)">EXIT VALUES</p>
  <div class="abs" style="left:26px;top:118px;width:190px;height:8px;background:var(--blue);display:grid;grid-template-columns:repeat(4,1fr);color:#fff;font-size:3.6px;text-align:center;line-height:8px;font-weight:700">
    <span>$165M</span><span>$250M/$500M*</span><span>$400M</span><span>$98M</span>
  </div>
  <footer class="foot"><span class="brand">Harlow</span><i class="foot-bar"></i></footer>
</section>

<section class="slide pillars" style="left:963px;top:190px">
  <p class="kicker">Place the sub header here</p><h2 class="title">Differentiated model: four pillars for success</h2><span class="num">10</span>
  <div class="band" style="left:0;top:46px;width:226px;height:30px"></div>
  <div class="abs" style="left:6px;top:50px;width:214px;display:grid;grid-template-columns:repeat(4,1fr);text-align:center;color:#fff;font-size:3.2px;font-weight:700">
    <div><svg width="12" height="12" aria-hidden="true"><circle cx="6" cy="4" r="2.5" fill="none" stroke="#fff" stroke-width=".7"/><path d="M2 11c0-3 8-3 8 0" fill="none" stroke="#fff" stroke-width=".7"/></svg><br>TEAM AND ADVISORY BOARD</div>
    <div><svg width="12" height="12" aria-hidden="true"><circle cx="6" cy="6" r="4.5" fill="none" stroke="#fff" stroke-width=".7"/><circle cx="6" cy="6" r="1.5" fill="#fff"/></svg><br>TARGET PROFILE</div>
    <div><svg width="12" height="12" aria-hidden="true"><path d="M2 6h8M7 3l3 3-3 3" fill="none" stroke="#fff" stroke-width=".7"/></svg><br>PROPRIETARY COMPANY / EXECUTIVE SOURCING</div>
    <div><svg width="12" height="12" aria-hidden="true"><circle cx="5" cy="5" r="3" fill="none" stroke="#fff" stroke-width=".7"/><line x1="7" y1="7" x2="10.5" y2="10.5" stroke="#fff" stroke-width=".8"/></svg><br>OPERATIONAL FOCUS</div>
  </div>
  <div class="abs" style="left:8px;top:80px;width:212px;display:grid;grid-template-columns:repeat(4,1fr);gap:4px">
    <ul class="tx"><li>Team with strong investment and technology backgrounds</li><li>Executive board recruitment</li><li>Proven founders and CEOs</li></ul>
    <ul class="tx"><li>Growth buyouts of high-growth software</li><li>Recurring revenue of 10M to 100M</li><li>Capital efficient businesses</li></ul>
    <ul class="tx"><li>Algorithmic approach screens 100K companies</li><li>Companies screened for timing</li><li>Regional high value events</li></ul>
    <ul class="tx"><li>Team building and operational focus</li><li>Control investments enable rapid change</li><li>Price discipline</li></ul>
  </div>
  <footer class="foot"><span class="brand">Harlow</span><i class="foot-bar"></i></footer>
</section>

<!-- Row 3 -->
<section class="slide pillars-pie" style="left:11px;top:371px">
  <p class="kicker">Place the sub header here</p><h2 class="title">Differentiated model: four pillars for success</h2><span class="num">11</span>
  <svg class="abs" style="left:6px;top:40px" width="104" height="104" aria-hidden="true">
    <path d="M52 52 L52 2 A50 50 0 0 0 2 52 Z" fill="var(--blue)"/>
    <path d="M52 52 L102 52 A50 50 0 0 0 52 2 Z" fill="var(--sky)"/>
    <path d="M52 52 L52 102 A50 50 0 0 0 102 52 Z" fill="var(--teal)"/>
    <path d="M52 52 L2 52 A50 50 0 0 0 52 102 Z" fill="#a8d8ea"/>
    <circle cx="52" cy="52" r="14" fill="#fff"/>
  </svg>
  <div class="abs" style="left:116px;top:28px;width:104px">
    <div class="cell-head">Team and Advisory Board</div>
    <ul class="tx"><li>Rated 10+ exits from our proprietary sourcing model</li><li>Advisory CEOs with broad operating experience</li></ul>
    <div class="cell-head">Operational Focus</div>
    <ul class="tx"><li>Hands-on playbook aligned with management</li><li>Incentive plans linked to value creation</li></ul>
    <div class="cell-head">Target Profile</div>
    <ul class="tx"><li>Transactions are a growth buyout with control</li><li>Strong recurring revenue</li></ul>
    <div class="cell-head">Proprietary Company / Executive Sourcing</div>
    <ul class="tx"><li>Proactive outreach reaches founders directly</li><li>Repeatable pipeline with high win rate</li></ul>
  </div>
  <footer class="foot"><span class="brand">Harlow</span><i class="foot-bar"></i></footer>
</section>

<section class="slide org-chart" style="left:249px;top:371px">
  <p class="kicker">Place the sub header here</p><h2 class="title">Team with strong investment and technology background</h2><span class="num">12</span>
  <svg class="abs" style="left:0;top:0" width="226" height="170" aria-hidden="true">
    <g stroke="var(--sky)" stroke-width=".5" fill="none">
      <path d="M77 38V44H190M77 44H18M50 44v6M18 44v6M82 44v6M114 44v6M150 44v6M190 44v6M190 38v6"/>
      <path d="M113 66v6M113 80v10M45 90h136M45 90v4M113 90v4M181 90v4"/>
    </g>
  </svg>
  <div class="box fill" style="left:62px;top:26px;width:30px;height:12px">Managing Director</div>
  <div class="box fill" style="left:174px;top:26px;width:32px;height:12px">Managing Director</div>
  <div class="box" style="left:4px;top:50px;width:30px;height:14px">Principal</div>
  <div class="box" style="left:36px;top:50px;width:30px;height:14px">Finance Director</div>
  <div class="box" style="left:68px;top:50px;width:30px;height:14px">Associate</div>
  <div class="box" style="left:100px;top:50px;width:30px;height:14px">Associate</div>
  <div class="box" style="left:134px;top:50px;width:32px;height:14px">Investment Advisor</div>
  <div class="box" style="left:172px;top:50px;width:36px;height:14px">Investment Advisor</div>
  <div class="box fill" style="left:66px;top:72px;width:94px;height:8px">Executive Advisory Board</div>
  <div class="box fill" style="left:20px;top:94px;width:50px;height:7px">Infrastructure Software</div>
  <div class="box fill" style="left:88px;top:94px;width:50px;height:7px">Vertical SaaS / Services</div>
  <div class="box fill" style="left:156px;top:94px;width:50px;height:7px">Horizontal SaaS</div>
  <div class="abs" style="left:8px;top:104px;width:210px;display:grid;grid-template-columns:repeat(3,1fr);gap:6px">
    <div style="display:grid;grid-template-columns:1fr 1fr;gap:1.5px"><span class="box" style="position:static">Advisor</span><span class="box" style="position:static">Advisor</span><span class="box" style="position:static">Advisor</span><span class="box" style="position:static">Advisor</span><span class="box" style="position:static">Advisor</span><span class="box" style="position:static">Advisor</span></div>
    <div style="display:grid;grid-template-columns:1fr 1fr;gap:1.5px"><span class="box" style="position:static">Advisor</span><span class="box" style="position:static">Advisor</span><span class="box" style="position:static">Advisor</span><span class="box" style="position:static">Advisor</span><span class="box" style="position:static">Advisor</span><span class="box" style="position:static">Advisor</span><span class="box" style="position:static">Advisor</span><span class="box" style="position:static">Advisor</span></div>
    <div style="display:grid;grid-template-columns:1fr 1fr;gap:1.5px"><span class="box" style="position:static">Advisor</span><span class="box" style="position:static">Advisor</span><span class="box" style="position:static">Advisor</span><span class="box" style="position:static">Advisor</span></div>
  </div>
  <footer class="foot"><span class="brand">Harlow</span><i class="foot-bar"></i></footer>
</section>

<section class="slide investors" style="left:487px;top:371px">
  <p class="kicker">Place the sub header here</p><h2 class="title">Team: Investors</h2><span class="num">13</span>
  <div class="abs" style="left:4px;top:40px;width:218px;display:grid;grid-template-columns:repeat(5,1fr);gap:4px;text-align:center">
    <div><div role="img" aria-label="Portrait of investor one" style="width:34px;height:34px;margin:0 auto;border-radius:50%;background:linear-gradient(#c9d3da,#8a99a5);border:1.5px solid var(--sky)"></div></div>
    <div><div role="img" aria-label="Portrait of investor two" style="width:34px;height:34px;margin:0 auto;border-radius:50%;background:linear-gradient(#c9d3da,#8a99a5);border:1.5px solid var(--sky)"></div></div>
    <div><div role="img" aria-label="Portrait of investor three" style="width:34px;height:34px;margin:0 auto;border-radius:50%;background:linear-gradient(#c9d3da,#8a99a5);border:1.5px solid var(--sky)"></div></div>
    <div><div role="img" aria-label="Portrait of investor four" style="width:34px;height:34px;margin:0 auto;border-radius:50%;background:linear-gradient(#c9d3da,#8a99a5);border:1.5px solid var(--sky)"></div></div>
    <div><div role="img" aria-label="Portrait of investor five" style="width:34px;height:34px;margin:0 auto;border-radius:50%;background:linear-gradient(#c9d3da,#8a99a5);border:1.5px solid var(--sky)"></div></div>
  </div>
  <div class="band" style="left:0;top:80px;width:226px;height:9px;display:grid;grid-template-columns:repeat(5,1fr);color:#fff;font-size:3.2px;font-weight:700;text-align:center;line-height:9px">
    <span>PARTNER</span><span>PARTNER</span><span>PRINCIPAL</span><span>ASSOCIATE</span><span>ASSOCIATE</span>
  </div>
  <div class="abs" style="left:6px;top:92px;width:214px;display:grid;grid-template-columns:repeat(5,1fr);gap:3px">
    <ul class="tx"><li>Joined in 2008</li><li>20 years in software investing</li><li>MBA, Halden Business School</li></ul>
    <ul class="tx"><li>Joined in 2008</li><li>15 years in growth equity</li><li>BA, Corrin College</li></ul>
    <ul class="tx"><li>Joined in 2012</li><li>Financial controller</li><li>CPA, Westmoor Institute</li></ul>
    <ul class="tx"><li>Joined in 2015</li><li>Led deal sourcing</li><li>BS, Ashgrove University</li></ul>
    <ul class="tx"><li>Joined in 2016</li><li>Capital markets</li><li>BA, Brantwell College</li></ul>
  </div>
  <footer class="foot"><span class="brand">Harlow</span><i class="foot-bar"></i></footer>
</section>

<section class="slide s-curve" style="left:725px;top:371px">
  <p class="kicker">Place the sub header here</p><h2 class="title">Lower middle market offers high value creation</h2><span class="num">14</span>
  <svg class="abs" style="left:6px;top:24px" width="214" height="130" aria-hidden="true">
    <text x="6" y="50" font-size="4" fill="#555" transform="rotate(-90 6 50)">Revenue</text>
    <line x1="20" y1="4" x2="20" y2="118" stroke="#999" stroke-width=".5"/>
    <line x1="20" y1="118" x2="210" y2="118" stroke="#999" stroke-width=".5"/>
    <rect x="20" y="90" width="40" height="28" fill="var(--mint)" opacity=".7"/>
    <rect x="60" y="36" width="60" height="82" fill="var(--cream)" opacity=".7"/>
    <path d="M22 112 C70 110 80 100 100 70 S150 30 205 24" fill="none" stroke="#e2b86a" stroke-width=".8"/>
    <text x="2" y="90" font-size="3.6" fill="#555">$25m</text><text x="6" y="106" font-size="3.6" fill="#555">$5m</text>
    <text x="168" y="126" font-size="3.8" fill="#555">Time / Stage</text>
  </svg>
  <footer class="foot"><span class="brand">Harlow</span><i class="foot-bar"></i></footer>
</section>

<section class="slide asset-class" style="left:963px;top:371px">
  <p class="kicker">Place the sub header here</p><h2 class="title">Growth buyouts/equity represent an attractive asset class</h2><span class="num">15</span>
  <div class="img-fill" role="img" aria-label="Dusk city skyline background band" style="left:0;top:26px;width:226px;height:76px;background:linear-gradient(180deg,#32526f,#6f94b3)"></div>
  <p class="abs" style="left:0;top:40px;width:226px;text-align:center;color:#fff;font-size:6px">Lower end of Growth Equity market is underserved:<br>(sub-$25M)</p>
  <div class="abs" style="left:8px;top:106px;width:212px;display:grid;grid-template-columns:repeat(3,1fr);gap:8px">
    <p class="tx">Early leaders have raised larger funds focusing on bigger transactions.</p>
    <p class="tx">Next generation funds have followed a similar path to larger deals.</p>
    <p class="tx">The segment has few established leaders and little competition.</p>
  </div>
  <p class="abs" style="left:0;top:126px;width:226px;text-align:center;color:var(--teal);font-size:4.5px">GROWTH EQUITY OFFERS AN ATTRACTIVE RISK/REWARD PROFILE</p>
  <p class="abs tx" style="left:12px;top:134px;width:202px;text-align:center;font-size:2.8px">Simply put, growth equity offers a similar return profile to leveraged buyouts but without the leverage, and could also be viewed as a lower-volatility version of venture capital returns.</p>
  <footer class="foot"><span class="brand">Harlow</span><i class="foot-bar"></i></footer>
</section>

<!-- Row 4 -->
<section class="slide buyouts" style="left:11px;top:553px">
  <p class="kicker">Place the sub header here</p><h2 class="title">Growth buyouts: attractive investments requiring unique expertise</h2><span class="num">16</span>
  <p class="abs tx" style="left:12px;top:30px;width:200px">Contrary to popular belief, lorem ipsum is not simply random text. It has roots in a piece of classical literature from 45 BC, making it over two thousand years old.</p>
  <svg class="abs" style="left:10px;top:56px" width="212" height="44" aria-hidden="true">
    <polygon points="0,0 200,0 206,6 200,12 0,12" fill="var(--blue)"/>
    <polygon points="30,14 200,14 206,20 200,26 30,26" fill="var(--sky)"/>
    <polygon points="60,28 200,28 206,34 200,40 60,40" fill="var(--teal)"/>
  </svg>
  <p class="abs" style="left:18px;top:59px;font-size:3.8px;color:#fff;font-weight:700">Growth buyouts: Requires Skills and Experience</p>
  <p class="abs" style="left:48px;top:73px;font-size:3.8px;color:#fff;font-weight:700">Differ from traditional buyouts</p>
  <p class="abs" style="left:78px;top:87px;font-size:3.8px;color:#fff;font-weight:700">Growth buyouts play to our strengths</p>
  <div class="abs" style="left:12px;top:104px;width:200px;display:grid;grid-template-columns:repeat(4,1fr);gap:4px">
    <p class="tx">Contrary to popular belief, lorem ipsum is not random text.</p>
    <p class="tx">Contrary to popular belief, lorem ipsum is not random text.</p>
    <p class="tx">Contrary to popular belief, lorem ipsum is not random text.</p>
    <p class="tx">Contrary to popular belief, lorem ipsum is not random text.</p>
  </div>
  <footer class="foot"><span class="brand">Harlow</span><i class="foot-bar"></i></footer>
</section>

<section class="slide focus" style="left:249px;top:553px">
  <p class="kicker">Place the sub header here</p><h2 class="title">Investment focus on large, high growth markets</h2><span class="num">17</span>
  <div class="abs" style="left:4px;top:36px;width:218px;height:116px;display:grid;grid-template-columns:repeat(3,1fr);gap:4px">
    <div style="background:var(--ice);position:relative"><p class="big-num" style="padding:4px">01</p><div class="cell-head" style="background:var(--blue);text-align:center;margin-top:8px">Infrastructure Software</div><ul class="tx" style="margin-top:6px"><li>Large move to the cloud</li><li>Realignment of datacenters</li></ul><div style="position:absolute;left:20px;bottom:6px;width:30px;height:6px;background:#cfd4d8"></div></div>
    <div style="background:var(--ice);position:relative"><p class="big-num" style="padding:4px">02</p><div class="cell-head" style="background:var(--blue);text-align:center;margin-top:8px">Vertical SaaS/ Services</div><ul class="tx" style="margin-top:6px"><li>Redefinition of business process</li><li>Domain knowledge is key</li></ul><div style="position:absolute;left:20px;bottom:6px;width:30px;height:6px;background:#cfd4d8"></div></div>
    <div style="background:var(--ice);position:relative"><p class="big-num" style="padding:4px">03</p><div class="cell-head" style="background:var(--blue);text-align:center;margin-top:8px">Horizontal SaaS</div><ul class="tx" style="margin-top:6px"><li>Large revenue opportunity</li><li>Large market cap leaders</li></ul><div style="position:absolute;left:20px;bottom:6px;width:30px;height:6px;background:#cfd4d8"></div></div>
  </div>
  <footer class="foot"><span class="brand">Harlow</span><i class="foot-bar"></i></footer>
</section>

<section class="slide sourcing" style="left:487px;top:553px">
  <p class="kicker">Place the sub header here</p><h2 class="title">Proprietary company and executive sourcing</h2><span class="num">18</span>
  <div class="band" style="left:0;top:30px;width:62px;height:118px"></div>
  <p class="abs" style="left:4px;top:34px;font-size:3.6px;color:#fff;font-weight:700">Investment Prospect:</p>
  <svg class="abs" style="left:14px;top:66px" width="34" height="34" aria-hidden="true"><circle cx="17" cy="17" r="15" fill="none" stroke="#fff" stroke-width="1"/><line x1="14" y1="10" x2="14" y2="20" stroke="#fff" stroke-width="1.6"/><line x1="20" y1="10" x2="20" y2="20" stroke="#fff" stroke-width="1.6"/><circle cx="14" cy="24" r="1" fill="#fff"/><circle cx="20" cy="24" r="1" fill="#fff"/></svg>
  <ul class="abs tx" style="left:66px;top:48px;width:46px"><li>Custom built algorithms</li><li>Screen 100K companies</li><li>Revenue size, growth and connections</li><li>Senior level outreach</li></ul>
  <div class="band" style="left:116px;top:30px;width:62px;height:118px;background:var(--sky)"></div>
  <p class="abs" style="left:120px;top:34px;font-size:3.6px;color:#fff;font-weight:700">Executive Identification:</p>
  <svg class="abs" style="left:130px;top:66px" width="34" height="34" aria-hidden="true"><circle cx="17" cy="17" r="15" fill="none" stroke="#fff" stroke-width="1"/><circle cx="17" cy="13" r="4" fill="#fff"/><path d="M9 25c2-6 14-6 16 0" fill="#fff"/></svg>
  <ul class="abs tx" style="left:180px;top:48px;width:42px"><li>Executive advisory board</li><li>15 years of M&amp;A history</li><li>Scalable, capital efficient</li><li>Early connections</li></ul>
  <footer class="foot"><span class="brand">Harlow</span><i class="foot-bar"></i></footer>
</section>

<section class="slide prospects" style="left:725px;top:553px">
  <p class="kicker">Place the sub header here</p><h2 class="title">Identification and prospect development</h2><span class="num">19</span>
  <p class="abs" style="left:62px;top:46px;font-size:4.2px;font-weight:700;color:#333">Company Universe</p>
  <svg class="abs" style="left:4px;top:52px" width="130" height="92" aria-hidden="true">
    <text x="4" y="70" font-size="3.6" fill="#555" transform="rotate(-90 4 70)"># of companies</text>
    <g fill="#555" font-size="3"><text x="8" y="6">90,000</text><text x="8" y="22">70,000</text><text x="8" y="38">50,000</text><text x="8" y="54">30,000</text><text x="8" y="70">10,000</text></g>
    <line x1="26" y1="2" x2="26" y2="82" stroke="#999" stroke-width=".5"/><line x1="26" y1="82" x2="128" y2="82" stroke="#999" stroke-width=".5"/>
    <rect x="38" y="16" width="12" height="66" fill="var(--navy)"/>
    <rect x="52" y="16" width="60" height="30" fill="var(--mint)"/>
    <rect x="52" y="50" width="50" height="22" fill="#b9dcee"/>
    <g fill="#555" font-size="3.2"><text x="32" y="89">&lt;$4M</text><text x="60" y="89">$4-8M</text><text x="80" y="89">$8-25M</text><text x="104" y="89">&gt;$25M</text></g>
  </svg>
  <p class="abs" style="left:56px;top:75px;font-size:3.6px;color:#333;width:60px;text-align:center">Need to mine large universe frequently</p>
  <p class="abs" style="left:56px;top:106px;font-size:3.6px;color:#333;width:50px;text-align:center">Develop relationships before reach target size</p>
  <p class="abs" style="left:68px;top:146px;font-size:4px;font-weight:700;color:#333">Revenue Range</p>
  <p class="abs" style="left:154px;top:46px;font-size:8px;color:#9aa4ab">Vectors</p>
  <ul class="abs tx" style="left:156px;top:58px"><li>Revenue Size</li><li>Growth Rate</li><li>Market Segment</li><li>Company Status</li></ul>
  <p class="abs" style="left:154px;top:90px;font-size:8px;color:#9aa4ab">Engagement</p>
  <ul class="abs tx" style="left:156px;top:102px"><li>Network Introductions</li><li>Dinner Series</li><li>Frequent Marketing</li><li>Outreach</li><li>Executive Connections</li></ul>
  <footer class="foot"><span class="brand">Harlow</span><i class="foot-bar"></i></footer>
</section>

<section class="slide top-prospects" style="left:963px;top:553px">
  <p class="kicker">Place the sub header here</p><h2 class="title">Top 1000 prospects by theme / growth rate</h2><span class="num">20</span>
  <table class="data" style="left:0;top:26px;width:226px;font-size:3.2px">
    <tr><th style="background:#fff"></th><th style="background:var(--navy)">Revenue Estimate $</th><th style="background:var(--blue)">Average Growth 16'</th><th>% of Top Prospects</th></tr>
    <tr><td style="font-weight:700;color:#333">THEME</td><td></td><td></td><td></td></tr>
    <tr><td>Security</td><td>7.2</td><td>145%</td><td>2%</td></tr>
    <tr><td>Healthcare</td><td>7.0</td><td>77%</td><td>7%</td></tr>
    <tr><td>Mobile</td><td>5.7</td><td>73%</td><td>9%</td></tr>
    <tr><td>Other</td><td>6.1</td><td>69%</td><td>7%</td></tr>
    <tr><td>E-commerce</td><td>5.8</td><td>65%</td><td>4%</td></tr>
    <tr><td>Consumer</td><td>4.9</td><td>62%</td><td>6%</td></tr>
    <tr><td>Education</td><td>6.2</td><td>59%</td><td>5%</td></tr>
    <tr><td>Cloud and System Software</td><td>7.2</td><td>59%</td><td>5%</td></tr>
    <tr><td>Software</td><td>5.9</td><td>57%</td><td>23%</td></tr>
    <tr><td>Data Analytics</td><td>5.4</td><td>56%</td><td>5%</td></tr>
    <tr><td>Financial</td><td>6.3</td><td>55%</td><td>4%</td></tr>
    <tr><td>Hardware</td><td>4.9</td><td>27%</td><td>1%</td></tr>
    <tr class="total"><td style="background:var(--sky);color:#fff">Total</td><td style="background:var(--sky);color:#fff">6.1</td><td style="background:var(--sky);color:#fff">62%</td><td style="background:var(--sky);color:#fff">100%</td></tr>
  </table>
  <footer class="foot"><span class="brand">Harlow</span><i class="foot-bar"></i></footer>
</section>

<!-- Row 5 -->
<section class="slide exec-db" style="left:11px;top:734px">
  <p class="kicker">Place the sub header here</p><h2 class="title">Executive sourcing / mining M&amp;A database</h2><span class="num">21</span>
  <div role="img" aria-label="Portrait of featured executive" class="img-fill" style="left:6px;top:26px;width:34px;height:40px;background:linear-gradient(#d6dde2,#8797a3)"></div>
  <p class="abs" style="left:44px;top:26px;font-size:4.2px;font-weight:700;color:#222">MARTIN OSTRANDER</p>
  <p class="abs tx" style="left:44px;top:32px;font-size:2.8px">Founder/CEO of Senior Executive Analytics</p>
  <p class="abs tx" style="left:44px;top:38px;width:60px">Funding: Raised ~$4m<br>Exit: Acquired by a US buyer for $150M in 2010<br>Ratio: 37x</p>
  <table class="data" style="left:4px;top:70px;width:96px;font-size:2.8px">
    <tr><td>Segment</td><td>Total # Exits</td><td>Avg Price</td></tr>
    <tr><td>Adtech</td><td>181</td><td>$149</td></tr><tr><td>Cloud and System</td><td>715</td><td>$314</td></tr>
    <tr><td>Consumer</td><td>1,655</td><td>$196</td></tr><tr><td>Data Analytics</td><td>616</td><td>$185</td></tr>
    <tr><td>E-commerce</td><td>468</td><td>$160</td></tr><tr><td>Education</td><td>264</td><td>$127</td></tr>
    <tr><td>Financial</td><td>805</td><td>$319</td></tr><tr><td>Hardware</td><td>1,288</td><td>$213</td></tr>
    <tr><td>Mobile</td><td>1,014</td><td>$272</td></tr><tr class="total"><td>Total</td><td>17,832</td><td>$217</td></tr>
  </table>
  <table class="data" style="left:110px;top:34px;width:112px;font-size:3.4px">
    <tr><th>Exit Ranges $m</th><th>% Total</th></tr>
    <tr><td style="padding:6px 3px">20-50</td><td>34%</td></tr>
    <tr><td style="padding:6px 3px">50-150</td><td>29%</td></tr>
    <tr><td style="padding:6px 3px">150-300</td><td>15%</td></tr>
    <tr><td style="padding:6px 3px">300-500</td><td>9%</td></tr>
    <tr><td style="padding:6px 3px">500+</td><td>13%</td></tr>
    <tr class="total"><td style="background:var(--sky);color:#fff">Total</td><td style="background:var(--sky);color:#fff">100%</td></tr>
  </table>
  <footer class="foot"><span class="brand">Harlow</span><i class="foot-bar"></i></footer>
</section>

<section class="slide geo-a" style="left:249px;top:734px">
  <p class="kicker">Place the sub header here</p><h2 class="title">Comprehensive geographic coverage</h2><span class="num">22</span>
  <div class="img-fill" role="img" aria-label="Grey world map with blue regional bubbles" style="left:6px;top:40px;width:140px;height:90px;background:radial-gradient(ellipse at 50% 50%,#e3e7ea,#f4f6f7 70%,#fff)"></div>
  <svg class="abs" style="left:6px;top:40px" width="140" height="90" aria-hidden="true">
    <circle cx="46" cy="30" r="9" fill="var(--blue)" opacity=".8"/><circle cx="100" cy="28" r="6" fill="var(--blue)" opacity=".8"/><circle cx="30" cy="60" r="7" fill="var(--sky)"/><circle cx="112" cy="60" r="5" fill="var(--sky)"/>
  </svg>
  <p class="abs" style="left:152px;top:42px;font-size:4.5px;color:#333">DESCRIPTION</p>
  <p class="abs tx" style="left:152px;top:50px;width:68px">There are many variations of passages available, but the majority have suffered alteration in some form.</p>
  <svg class="abs" style="left:152px;top:74px" width="60" height="14" aria-hidden="true"><circle cx="7" cy="7" r="6" fill="none" stroke="var(--navy)" stroke-width="2"/><circle cx="36" cy="7" r="6" fill="none" stroke="var(--blue)" stroke-width="2"/></svg>
  <svg class="abs" style="left:152px;top:94px" width="60" height="20" aria-hidden="true"><rect x="0" y="14" width="8" height="6" fill="var(--sky)"/><rect x="10" y="8" width="8" height="12" fill="var(--blue)"/><rect x="20" y="2" width="8" height="18" fill="var(--navy)"/></svg>
  <p class="abs tx" style="left:8px;top:142px">■ KEYWORD &nbsp; ■ KEYWORD &nbsp; ■ KEYWORD &nbsp; ■ KEYWORD</p>
  <footer class="foot"><span class="brand">Harlow</span><i class="foot-bar"></i></footer>
</section>

<section class="slide geo-b" style="left:487px;top:734px">
  <p class="kicker">Place the sub header here</p><h2 class="title">Comprehensive geographic coverage</h2><span class="num">23</span>
  <div class="img-fill" role="img" aria-label="World map with regions shaded in blues and teals" style="left:8px;top:40px;width:142px;height:88px;background:linear-gradient(120deg,#1d5e99,#33a6d7 50%,#86cfc6)"></div>
  <div class="abs" style="left:156px;top:40px;width:64px">
    <p class="hd" style="font-weight:400;color:var(--navy)">90% Growth</p><p class="tx">There are many variations of passages.</p>
    <p class="hd" style="font-weight:400;color:var(--navy)">75% Growth</p><p class="tx">There are many variations of passages.</p>
    <p class="hd" style="font-weight:400;color:var(--navy)">60% Growth</p><p class="tx">There are many variations of passages.</p>
    <p class="hd" style="font-weight:400;color:var(--navy)">50% Growth</p><p class="tx">There are many variations of passages.</p>
  </div>
  <p class="abs tx" style="left:40px;top:138px">■ NORTH AMERICA &nbsp; ■ LATIN AMERICA &nbsp; ■ AFRICA &nbsp; ■ ASIA &nbsp; ■ EUROPE &nbsp; ■ AUSTRALIA</p>
  <footer class="foot"><span class="brand">Harlow</span><i class="foot-bar"></i></footer>
</section>

<section class="slide geo-c" style="left:725px;top:734px">
  <p class="kicker">Place the sub header here</p><h2 class="title">Comprehensive geographic coverage</h2><span class="num">24</span>
  <div class="img-fill" role="img" aria-label="Grey world map with percentage callouts" style="left:20px;top:28px;width:186px;height:76px;background:radial-gradient(ellipse,#d4d8db,#eef0f2 70%,#fff)"></div>
  <p class="abs tx" style="left:30px;top:108px">■ KEYWORD &nbsp;&nbsp; ■ KEYWORD &nbsp;&nbsp; ■ KEYWORD &nbsp;&nbsp; ■ KEYWORD</p>
  <svg class="abs" style="left:12px;top:118px" width="100" height="36" aria-hidden="true">
    <rect x="10" y="2" width="80" height="6" fill="var(--navy)"/><rect x="10" y="10" width="60" height="6" fill="var(--blue)"/><rect x="10" y="18" width="44" height="6" fill="var(--sky)"/><rect x="10" y="26" width="30" height="6" fill="var(--mint)"/>
  </svg>
  <p class="abs" style="left:124px;top:118px;font-size:4.5px;color:#333">DESCRIPTION</p>
  <p class="abs tx" style="left:124px;top:125px;width:94px">There are many variations of passages available, but most have suffered alteration in some form.</p>
  <footer class="foot"><span class="brand">Harlow</span><i class="foot-bar"></i></footer>
</section>

<section class="slide playbook" style="left:963px;top:734px">
  <p class="kicker">Place the sub header here</p><h2 class="title">Northvale Growth's sourcing playbook</h2><span class="num">25</span>
  <div class="box fill" style="left:12px;top:40px;width:50px;height:7px">Screen Large Universe</div>
  <p class="abs tx" style="left:12px;top:50px;width:50px;text-align:center">Proprietary technology used to identify best prospects</p>
  <p class="abs tx" style="left:12px;top:66px;width:50px;text-align:center">Screen 100K companies every 3 weeks</p>
  <div class="box fill" style="left:12px;top:82px;width:50px;height:7px">Identify Executives from M&amp;A</div>
  <p class="abs tx" style="left:12px;top:92px;width:50px;text-align:center">Screen for high value exits and capital raised</p>
  <div class="box fill" style="left:74px;top:40px;width:50px;height:7px;background:var(--sky);border-color:var(--sky)">Identify Top Prospects</div>
  <p class="abs tx" style="left:74px;top:50px;width:50px;text-align:center">Outbound network introductions to engage prospects</p>
  <p class="abs tx" style="left:74px;top:66px;width:50px;text-align:center">1K top prospects selected by analytical model</p>
  <div class="box fill" style="left:74px;top:82px;width:50px;height:7px;background:var(--sky);border-color:var(--sky)">Advisory board / Top Executives</div>
  <p class="abs tx" style="left:74px;top:94px;width:50px;text-align:center">Develop / Source executive talent</p>
  <p class="abs" style="left:150px;top:38px;font-size:3.6px;font-weight:700;color:#333">Prospects/Executives by Region</p>
  <div class="img-fill" role="img" aria-label="Small US map with regional dots" style="left:148px;top:46px;width:72px;height:30px;background:radial-gradient(ellipse,#d5e6ef,#f2f7fa 75%,#fff)"></div>
  <p class="abs" style="left:156px;top:80px;font-size:3.2px;font-weight:700;color:#333">US Term Sheet / LOI's Issued</p>
  <svg class="abs" style="left:164px;top:88px" width="40" height="40" aria-hidden="true"><circle cx="20" cy="20" r="18" fill="var(--sky)"/><path d="M20 20 L20 2 A18 18 0 0 1 36 28 Z" fill="var(--navy)"/><path d="M20 20 L36 28 A18 18 0 0 1 14 37 Z" fill="var(--blue)"/></svg>
  <div class="box fill" style="left:112px;top:116px;width:22px;height:7px">Results</div>
  <footer class="foot"><span class="brand">Harlow</span><i class="foot-bar"></i></footer>
</section>

<!-- Row 6 -->
<section class="slide execution" style="left:11px;top:916px">
  <p class="kicker">Place the sub header here</p><h2 class="title">Northvale Growth's execution model</h2><span class="num">26</span>
  <div class="abs" style="left:0;top:26px;width:226px;height:128px;display:grid;grid-template-columns:40px 1fr 1fr 1fr;grid-template-rows:8px 1fr 1fr 1fr">
    <span></span>
    <span style="background:var(--blue);color:#fff;font-size:4px;text-align:center;line-height:8px;font-weight:700">Investment</span>
    <span style="background:var(--sky);color:#fff;font-size:4px;text-align:center;line-height:8px;font-weight:700">Execution</span>
    <span style="background:var(--teal);color:#fff;font-size:4px;text-align:center;line-height:8px;font-weight:700">Exit</span>
    <span style="background:var(--blue);color:#fff;font-size:4px;display:flex;align-items:center;justify-content:center">Company</span>
    <ul class="tx" style="background:var(--ice);margin:0;padding:3px 3px 3px 8px"><li>$5-50M revenue, 30-100% growth</li><li>Capital efficient</li></ul>
    <ul class="tx" style="background:var(--ice);margin:0;padding:3px 3px 3px 8px"><li>Scale revenue 3-5x</li><li>Professionalize the organization</li><li>EBITDA scale</li></ul>
    <ul class="tx" style="background:var(--ice);margin:0;padding:3px 3px 3px 8px"><li>Maintain 30%+ revenue growth</li><li>#1 or 2 in its market</li></ul>
    <span style="background:var(--sky);color:#fff;font-size:4px;display:flex;align-items:center;justify-content:center">Northvale</span>
    <ul class="tx" style="margin:0;padding:3px 3px 3px 8px"><li>$15M to $25M primary</li><li>Control / significant minority</li></ul>
    <ul class="tx" style="margin:0;padding:3px 3px 3px 8px"><li>Sales and marketing</li><li>Strategy and positioning</li><li>Recruiting</li></ul>
    <ul class="tx" style="margin:0;padding:3px 3px 3px 8px"><li>Achieve 3x at 30% IRR</li><li>Downside protection</li><li>Upside potential</li></ul>
    <span style="background:var(--teal);color:#fff;font-size:4px;display:flex;align-items:center;justify-content:center">Executive</span>
    <ul class="tx" style="background:var(--ice);margin:0;padding:3px 3px 3px 8px"><li>Add CXO / Executive Chairman</li><li>Co-invest $500K</li></ul>
    <ul class="tx" style="background:var(--ice);margin:0;padding:3px 3px 3px 8px"><li>Prior experience</li><li>Wolf pack / board</li><li>Relationships</li></ul>
    <ul class="tx" style="background:var(--ice);margin:0;padding:3px 3px 3px 8px"><li>Founder economics</li><li>Reward profile</li></ul>
  </div>
  <footer class="foot"><span class="brand">Harlow</span><i class="foot-bar"></i></footer>
</section>

<section class="slide protection" style="left:249px;top:916px">
  <p class="kicker">Place the sub header here</p><h2 class="title">Equity protection with upside option</h2><span class="num">27</span>
  <svg class="abs" style="left:8px;top:24px" width="212" height="132" aria-hidden="true">
    <text x="5" y="90" font-size="3.6" fill="#555" transform="rotate(-90 5 90)">Investment Multiple</text>
    <line x1="12" y1="4" x2="12" y2="116" stroke="#999" stroke-width=".5"/><line x1="12" y1="116" x2="210" y2="116" stroke="#999" stroke-width=".5"/>
    <rect x="28" y="96" width="10" height="20" fill="var(--navy)"/>
    <rect x="40" y="70" width="8" height="46" fill="var(--navy)"/>
    <path d="M40 70 L90 46" stroke="var(--navy)" stroke-width=".6"/>
    <rect x="96" y="50" width="10" height="66" fill="var(--sky)"/>
    <rect x="108" y="30" width="8" height="86" fill="var(--sky)"/>
    <rect x="150" y="36" width="10" height="80" fill="var(--mint)"/>
    <rect x="162" y="12" width="8" height="104" fill="var(--mint)"/>
    <text x="24" y="66" font-size="3.6" font-weight="700" fill="#333">FINANCIAL</text>
    <text x="88" y="26" font-size="3.6" font-weight="700" fill="#333">OPERATIONAL</text>
    <text x="146" y="8" font-size="3.6" font-weight="700" fill="#333">STRATEGIC</text>
    <g font-size="3.2" fill="#555"><text x="20" y="124">Downside Risk Protection</text><text x="88" y="124">Base Case Fundamentals</text><text x="146" y="124">Game Changing Opportunities</text></g>
  </svg>
  <ul class="abs tx" style="left:58px;top:96px;width:38px"><li>Preferred instrument</li><li>Return structured</li></ul>
  <ul class="abs tx" style="left:126px;top:70px;width:36px"><li>Increase revenue growth</li><li>Expand business</li><li>Transfer innovation</li></ul>
  <ul class="abs tx" style="left:180px;top:50px;width:40px"><li>Competitive repositioning</li><li>New innovation</li><li>Acquisitions</li></ul>
  <footer class="foot"><span class="brand">Harlow</span><i class="foot-bar"></i></footer>
</section>

<section class="slide conclusions" style="left:487px;top:916px">
  <span class="num">28</span>
  <div class="band" style="left:0;top:52px;width:80px;height:7px;background:var(--sky)"></div>
  <p class="kicker" style="left:80px;top:42px">Place the sub header here</p>
  <h2 class="title" style="left:80px;top:50px">Conclusions</h2>
  <ul class="abs tx" style="left:86px;top:68px;width:132px;font-size:3.6px;line-height:1.6">
    <li>Cohesive team with 20+ years of working together</li>
    <li>Compelling opportunity in lower-middle market buyouts and growth equity in private, recurring revenue software companies</li>
    <li>Repeatable, proprietary, analytics-driven model for sourcing executives and investment prospects</li>
    <li>Proven ability to deliver above market, risk-balanced returns of 3-5x</li>
  </ul>
  <footer class="foot"><span class="brand">Harlow</span><i class="foot-bar"></i></footer>
</section>

<section class="slide legal" style="left:725px;top:916px">
  <p class="kicker">Place the sub header here</p><h2 class="title">Important Information</h2><span class="num">29</span>
  <div class="abs" style="left:10px;top:22px;width:206px;font-size:2.6px;line-height:1.35;color:#555">
    <p style="margin:0 0 2px;font-weight:700">Definition of Gross Returns</p>
    <p style="margin:0 0 3px">Gross returns are calculated on investments made by the fund over its life. Returns shown do not reflect fees, expenses and carried interest, which will reduce actual returns to investors. Cash flows are aggregated at the deal level and compounded over the holding period.</p>
    <p style="margin:0 0 2px;font-weight:700">Definition of Net Returns</p>
    <p style="margin:0 0 3px">Net returns reflect the deduction of management fees, fund expenses and carried interest. Individual investor returns may vary with timing of capital calls and distributions.</p>
    <p style="margin:0 0 2px;font-weight:700">Aggregate Returns</p>
    <p style="margin:0 0 3px">Aggregate returns combine all portfolio companies held during the period. Unrealized positions are valued at estimated fair value and may differ from final outcomes. There is no assurance unrealized investments will be realized at the valuations shown.</p>
    <p style="margin:0 0 2px;font-weight:700">Benchmark Data</p>
    <p style="margin:0 0 3px">Benchmark figures are drawn from third-party sources believed reliable but not independently verified. Comparisons are for reference only and do not imply similar results.</p>
    <p style="margin:0">Past performance is not indicative of future results. All investments involve risk, including the loss of principal invested.</p>
  </div>
  <footer class="foot"><span class="brand">Harlow</span><i class="foot-bar"></i></footer>
</section>

<section class="slide legal" style="left:963px;top:916px">
  <p class="kicker">Place the sub header here</p><h2 class="title">Important Information</h2><span class="num">30</span>
  <div class="abs" style="left:12px;top:24px;width:202px;font-size:2.8px;line-height:1.45;color:#555;text-transform:uppercase">
    <p style="margin:0 0 3px">This presentation has been prepared solely for use by prospective investors of the fund and shall be maintained in strict confidence. Any reproduction or distribution in whole or in part is prohibited.</p>
    <p style="margin:0 0 3px">This presentation has been prepared in connection with a private offering to accredited investors of limited partnership interests. Such interests will be offered only by means of the definitive fund documents.</p>
    <p style="margin:0 0 3px">This presentation does not constitute an offer to sell or a solicitation of an offer to buy any interest in any jurisdiction where it is unlawful. Interests have not been registered under the securities laws of any state.</p>
    <p style="margin:0">Prospective investors should rely only on the definitive documents and consult their own advisors regarding legal, tax and financial consequences of an investment in the fund.</p>
  </div>
  <footer class="foot"><span class="brand">Harlow</span><i class="foot-bar"></i></footer>
</section>

</main>
</body>
</html>
```